Thornbury Building Company - Card Design

I am looking to use the logo designs that you already did for me to develop a business card. I would like the card to have a black background and be double sided. I want white and green logo and text. I have attached an inspiration photo of a look that I like. I would like to use the Vertical Logo attached to take up the full front side of the card. On the back where I have my name and information, I would like to have the horizontal logo or maybe even just the image of the 'A' and trees without the text. I am open, but I am looking for something clean and simple and I want the green to really pop! Additional files can be found under Design #: 58302946

Target Market(s)

Homeowners

Industry/Entity Type

Construction

Contact Information for Business Card

Name: Marcus Thornbury, Title: Project Manager, Phone: 555.274.8136, Email: thornburybuildingcompany@mailvesta.com, address: 487 Larkspur Ln, Ridgeford, CA 95033, Lic# 2468317

Colors
00AB8E
00BBA5
67D7C9
C6EFE9
E9F9F6

Requirements
Nice to have
• I would like to see the logos that I have already got from ArtLoomHub, though I am open to new ones

```html
<!DOCTYPE html>
<html lang="en">
<head>
<meta charset="UTF-8">
<title>Thornbury Building Company – Business Card</title>
<link rel="stylesheet" href="https://fonts.googleapis.com/css2?family=Montserrat:wght@400;500;600;700&display=swap">
<style>
  :root {
    --backdrop: #ececec;
    --card: #242424;
    --green: #5db543;
    --white: #ffffff;
    --soft-white: #e8e8e8;
    --pattern-light: #7a7a7a;
    --pattern-dark: #151515;
  }
  * { margin: 0; padding: 0; box-sizing: border-box; }
  html, body {
    width: 900px; height: 1200px; overflow: hidden;
    background: var(--backdrop);
    font-family: "Montserrat", Arial, sans-serif;
  }
  .canvas { position: relative; width: 900px; height: 1200px; }

  .card {
    position: absolute; left: 80px; width: 742px; height: 440px;
    border-radius: 36px; overflow: hidden;
    background: var(--card);
  }
  .card--front { top: 132px; }
  .card--back { top: 638px; height: 442px; }

  /* Front: brand block */
  .brand {
    position: absolute; left: 44px; top: 180px; width: 260px;
    text-align: center; color: var(--white); font-weight: 600;
  }
  .brand__mark {
    display: block; width: 46px; height: 46px; margin: 0 auto 18px;
    background: var(--green);
  }
  .brand__name { font-size: 32px; letter-spacing: 1px; line-height: 1; }
  .brand__sub { font-size: 13px; letter-spacing: 3.2px; margin-top: 8px; }

  .divider {
    position: absolute; left: 335px; top: 150px; width: 2px; height: 191px;
    background: var(--green);
  }

  /* Front: contact details */
  .details { position: absolute; left: 372px; top: 144px; width: 340px; color: var(--soft-white); }
  .details__name { font-size: 27px; font-weight: 700; color: var(--green); line-height: 1.1; }
  .details__title { font-size: 16px; font-weight: 500; margin-top: 2px; }
  .details__licence { font-size: 16px; font-weight: 600; margin-top: 18px; color: var(--white); }
  .details__licence span { color: var(--green); font-weight: 500; }
  .details__contact { list-style: none; margin-top: 16px; font-size: 14px; }
  .details__contact li { display: flex; align-items: center; gap: 10px; height: 23px; white-space: nowrap; }
  .details__contact svg { width: 15px; height: 15px; flex: none; }
  .details__address { font-size: 16px; margin-top: 14px; line-height: 1.25; }

  /* Back */
  .back-pattern {
    position: absolute; inset: 0;
    background: linear-gradient(100deg, var(--pattern-light) 0%, #3c3c3c 38%, #1e1e1e 62%, var(--pattern-dark) 100%);
  }
  .back-brand {
    position: absolute; right: 52px; top: 306px; text-align: right;
    color: var(--green); font-weight: 600; font-size: 15px; line-height: 1.2;
  }
</style>
</head>
<body>
<main class="canvas">

  <section class="card card--front" aria-label="Card front">
    <div class="brand">
      <span class="brand__mark"></span>
      <div class="brand__name">THORNBURY</div>
      <div class="brand__sub">BUILDING COMPANY</div>
    </div>

    <div class="divider"></div>

    <div class="details">
      <h1 class="details__name">Marcus Thornbury</h1>
      <p class="details__title">Project Manager</p>
      <p class="details__licence"><span>Lic</span> #2468317</p>
      <ul class="details__contact">
        <li>
          <svg viewBox="0 0 16 16" aria-hidden="true"><path fill="#5db543" d="M2 5c0-2 2-3 6-3s6 1 6 3v1h-3V5H5v1H2zM4 7h8l2 7H2zm4 1.6a2.2 2.2 0 1 0 0 4.4 2.2 2.2 0 0 0 0-4.4z"/></svg>
          555.274.8136
        </li>
        <li>
          <svg viewBox="0 0 16 16" aria-hidden="true"><path fill="#5db543" d="M1 3h14v1.2L8 9 1 4.2zM1 5.8l7 4.8 7-4.8V13H1z"/></svg>
          thornburybuildingcompany@mailvesta.com
        </li>
      </ul>
      <p class="details__address">487 Larkspur Ln, Ridgeford<br>CA 95033</p>
    </div>
  </section>

  <section class="card card--back" aria-label="Card back">
    <div class="back-pattern" role="img" aria-label="Repeating brand pattern fading from grey to black"></div>
    <div class="back-brand">Thornbury<br>Building Company</div>
  </section>

</main>
</body>
</html>
```